I need a book cover designed for "Generous Momentum. Where Winning Falls Short." The book encourages businesses to take up a social mission (that is, to have a social impact, such as corporate social responsibility.) in doing so, they find a greater sense of purpose, their employees and the community are more engaged, and their business grows. I use stories from my podcast Civic Purpose Uprising. 2 key word/phrases that may help t think about are Philanthropy and Corporate Social Responsibility.
This book will be followed by 1 or 2 other books. Another seies of books will also soon requre work.

The market is Mid-sized business owners and CEOs. They have built up the business to a successful place but now find that doesn't bring fulfilment or happiness. The cover needs to have a business or corporate feel.
The Colouring of the book, focus on blues and purples.
This will be a thin book - a quick and easy read of around 110 pages. It is 5x8 inches.
I would be happy to have a photo of me incorporated, but not the focus. I could have a photo done as directed by the designer, as I am planning to have a photoshoot done soon.
Fonts - Please chose a font with the rounded "a", such as in the Century Gothic font, however, open to suggestions.
The back cover will include:
o A book blurb – still to be written
o 2 or 3 endorsements
o Publishing logo (as it is my own publishing company.
o ISBN and barcode
On the spine
• Generous Momentum
• Melissa Garrow
• Publisher logo icon

For your interest: Melissa is a Speaker, Author, podcaster and Trusted Advisor to Authentic Influencers. Through nourishing community, Melissa maximises the potential of business and influences change.

Target Market(s)

The market is Mid-sized business owners and CEOs. They have built up the business to a successful place but now find that doesn't bring fulfillment or happiness. The cover needs to have a business or corporate feel.

Industry/Entity Type

This is business/corporate book

Font styles to use
Other font styles liked:
• Please chose a font with the rounded "a", such as in the Century Gothic font, however, open to suggestions.

Colors
0054AA
0677BA
7BADD7
CADEEF
E8F1F8
A7469A
B969AE
D3A5CF
EDDBEB
F8F0F9
6B429C
8869AF
B7A5CE
E3DAEB
F3F0F8

Requirements
Must have
• An eye catching design with a business feel.
Nice to have
• I would be nice to edit me into the cover somehow - like Brambleton puts himself in the background of his movies. I can have photos taken to match .

```html
<!DOCTYPE html>
<html lang="en">
<head>
<meta charset="utf-8">
<title>Generous Momentum — Book Cover</title>
<link href="https://fonts.googleapis.com/css2?family=Montserrat:wght@700&family=Questrial&display=swap" rel="stylesheet">
<style>
  :root {
    --backdrop: #9dd3c0;
    --cover-light: #7fd6ea;
    --cover-mid: #6cb8e6;
    --cover-violet: #7a86e0;
    --cover-lilac: #9a8ee3;
    --ink: #ffffff;
    --art-tone: rgba(255, 255, 255, 0.22);
  }
  * { margin: 0; padding: 0; box-sizing: border-box; }
  html, body {
    width: 1200px;
    height: 857px;
    overflow: hidden;
    background: var(--backdrop);
  }
  .canvas {
    position: relative;
    width: 1200px;
    height: 857px;
  }
  .cover {
    position: absolute;
    left: 390px;
    top: 120px;
    width: 420px;
    height: 616px;
    overflow: hidden;
    color: var(--ink);
    text-align: center;
    background:
      radial-gradient(ellipse 60% 40% at 70% 20%, var(--cover-violet) 0%, transparent 70%),
      radial-gradient(ellipse 50% 35% at 20% 45%, var(--cover-lilac) 0%, transparent 70%),
      radial-gradient(ellipse 55% 30% at 60% 85%, var(--cover-violet) 0%, transparent 70%),
      radial-gradient(ellipse 70% 40% at 40% 65%, var(--cover-light) 0%, transparent 75%),
      linear-gradient(160deg, var(--cover-light) 0%, var(--cover-mid) 50%, var(--cover-light) 100%);
  }
  .title {
    position: absolute;
    top: 36px;
    left: 0;
    width: 100%;
    font-family: "Montserrat", sans-serif;
    font-weight: 700;
    line-height: 1;
  }
  .title-line-one {
    display: block;
    font-size: 34px;
    letter-spacing: 5px;
    padding-left: 5px;
  }
  .title-line-two {
    display: block;
    margin-top: 8px;
    font-size: 25px;
    letter-spacing: 17px;
    padding-left: 17px;
  }
  .hero-art {
    position: absolute;
    left: 0;
    top: 176px;
    width: 420px;
    height: 214px;
  }
  .subtitle {
    position: absolute;
    top: 400px;
    left: 0;
    width: 100%;
    font-family: "Questrial", sans-serif;
    line-height: 1;
  }
  .subtitle-top {
    display: block;
    font-size: 19px;
    letter-spacing: 2px;
  }
  .subtitle-divider {
    display: flex;
    align-items: center;
    justify-content: center;
    gap: 8px;
    margin: 7px auto 6px;
    width: 192px;
    font-size: 12px;
    letter-spacing: 1px;
  }
  .subtitle-divider::before,
  .subtitle-divider::after {
    content: "";
    flex: 1;
    height: 1px;
    background: var(--ink);
  }
  .subtitle-bottom {
    display: block;
    font-size: 24px;
    letter-spacing: 1px;
  }
  .author {
    position: absolute;
    top: 560px;
    left: 0;
    width: 100%;
    font-family: "Montserrat", sans-serif;
    font-weight: 700;
    font-size: 24px;
    letter-spacing: 6px;
    padding-left: 6px;
    line-height: 1;
  }
</style>
</head>
<body>
  <main class="canvas">
    <section class="cover">
      <h1 class="title">
        <span class="title-line-one">GENEROUS</span>
        <span class="title-line-two">MOMENTUM</span>
      </h1>

      <svg class="hero-art" role="img" aria-label="Line illustration of an adult hand and a child's hand holding a single flower between them" viewBox="0 0 420 214">
        <defs>
          <radialGradient id="art-glow" cx="50%" cy="50%" r="55%">
            <stop offset="0%" stop-color="var(--art-tone)"/>
            <stop offset="100%" stop-color="rgba(255,255,255,0)"/>
          </radialGradient>
        </defs>
        <rect width="420" height="214" fill="url(#art-glow)"/>
      </svg>

      <h2 class="subtitle">
        <span class="subtitle-top">WHERE WINNING</span>
        <span class="subtitle-divider">FALLS</span>
        <span class="subtitle-bottom">SHORT</span>
      </h2>

      <p class="author">MELISSA GARROW</p>
    </section>
  </main>
</body>
</html>
```